Judicial election website to attract voters

I need a simple one-page web design for a judicial election. I'm going to put up one picture, maybe two. The picture I have needs a little touch-up (whiten teeth for example). I have 3 paragraphs of text. I'd like a "Donate" button that can link to a CoinDrift account. I'd also like a little background design, like the Constitution or something like that. There's a couple other little things but that's the bulk of it.

Target Market(s)

Involved voters and some media

Industry/Entity Type

Legal

Number of Pages Required

1 page

Font styles to use
Sans Serif

Requirements
Must have
• My picture, text, donate button
• Phrase "Remember to vote August 30, 2016!"
Nice to have
• Perhaps a second photo, maybe a short 30 second video of me talking directly to the voters, cool background: Constitution, something judgey.
Should not have
• Not sure ... profanity, I guess.

```html
<!DOCTYPE html>
<html lang="en">
<head>
<meta charset="utf-8">
<title>Lorem Ipsum – Local Election</title>
<link href="https://fonts.googleapis.com/css2?family=Jost:wght@400;500&family=Lato:wght@400&display=swap" rel="stylesheet">
<style>
  :root{
    --accent:#f15a3b;
    --slate:#5b6170;
    --ink:#333333;
    --rule:#c9c9c9;
    --footer:#000000;
    --white:#ffffff;
  }
  *{margin:0;padding:0;box-sizing:border-box}
  html,body{width:1200px;height:933px;overflow:hidden;background:var(--white)}
  body{position:relative;font-family:"Lato",sans-serif;color:var(--ink)}

  .site-header{position:absolute;top:0;left:0;width:1200px;height:80px;border-top:3px solid var(--accent);text-align:center}
  .brand{font-family:"Jost",sans-serif;font-weight:400;font-size:28px;line-height:80px;letter-spacing:.5px;color:var(--slate);margin-top:-5px}
  .brand span{color:var(--accent)}

  .hero{position:absolute;top:80px;left:0;width:1200px;height:472px;overflow:hidden}
  .hero-scene{position:absolute;inset:0;background:
      radial-gradient(circle at 25% 30%,rgba(190,120,110,.55),transparent 45%),
      radial-gradient(circle at 60% 20%,rgba(150,90,110,.5),transparent 40%),
      linear-gradient(180deg,#5a2e3a 0%,#3a1c24 55%,#6b3a22 85%,#8a5a35 100%)}
  .hero-portrait{position:absolute;right:0;top:42px;width:400px;height:430px;
      background:linear-gradient(180deg,#d9cfc4 0%,#d79b84 45%,#e98a6c 100%);border-radius:180px 180px 0 0}
  .vote-tag{position:absolute;left:99px;top:276px;width:505px;height:49px;background:var(--accent);border-left:4px solid var(--white);
      font-family:"Jost",sans-serif;font-size:27px;color:var(--white);line-height:49px;padding-left:18px}
  .slider-dots{position:absolute;top:438px;left:572px;display:flex;gap:8px}
  .slider-dots i{width:14px;height:14px;border:2px solid var(--white);border-radius:50%;display:block}
  .slider-dots i.active{background:var(--accent)}

  .columns{position:absolute;top:583px;left:0;width:1200px}
  .col{position:absolute;top:0;width:272px}
  .col-about{left:99px}
  .col-video{left:471px}
  .col-points{left:846px}
  .divider{position:absolute;top:0;width:1px;height:262px;background:linear-gradient(180deg,transparent,#e8e8e8 20%,#e8e8e8 80%,transparent)}
  .col-title{font-family:"Jost",sans-serif;font-weight:400;font-size:22px;color:var(--accent);height:45px;line-height:36px;border-bottom:1px solid var(--rule);position:relative}
  .col-title::after{content:"";position:absolute;left:0;bottom:-1px;width:64px;height:2px;background:var(--accent)}
  .col-about p{margin-top:12px;font-size:14px;line-height:22px;letter-spacing:.4px}

  .video-frame{margin-top:11px;width:279px;height:200px;border:1px solid #e2e2e2;padding:4px}
  .video-still{width:100%;height:100%;position:relative;background:linear-gradient(135deg,#2c3340 0%,#4a4f58 40%,#d9d2c6 70%,#3a2a20 100%)}
  .video-still svg{position:absolute;left:50%;top:50%;transform:translate(-50%,-50%)}

  .points{list-style:none;margin-top:11px}
  .points li{font-size:13.5px;height:32.6px;line-height:32.6px;display:flex;align-items:center;gap:11px}

  .site-footer{position:absolute;left:0;top:883px;width:1200px;height:50px;background:var(--footer)}
  .copyright{position:absolute;left:99px;top:0;line-height:50px;font-family:"Jost",sans-serif;font-size:13.5px;color:var(--white)}
  .donate{position:absolute;left:992px;top:8px;width:109px;height:35px;background:var(--accent);border:1.5px solid var(--white);
      font-family:"Jost",sans-serif;font-size:14.5px;color:var(--white);text-align:center;line-height:32px;text-decoration:none}
</style>
</head>
<body>
  <header class="site-header">
    <div class="brand">LOREM <span>IPSUM</span></div>
  </header>

  <section class="hero">
    <div class="hero-scene" role="img" aria-label="Scales of justice, gavel and law books on a warm bokeh background"></div>
    <div class="hero-portrait" role="img" aria-label="Portrait of the judicial candidate"></div>
    <div class="vote-tag">Remember To Vote August 30, 2016!</div>
    <div class="slider-dots"><i></i><i class="active"></i><i></i></div>
  </section>

  <main class="columns">
    <div class="divider" style="left:421px"></div>
    <div class="divider" style="left:795px"></div>

    <section class="col col-about">
      <h2 class="col-title">Lorem Ipsum Dolor</h2>
      <p>Lorem ipsum dolor sit amet, consectetuer adipiscing elit, sed diam nonummy nibh euismod tincidunt ut laoreet dolore magna aliquam erat volutpat. Ut wisi enim ad minim veniam, quis nostrud exerci exerci tation ullamcorper suscipit lobortis nisl ut aliquip ex ea commodo consequat. Duis autem vel eum iriure dolor in hendrerit Duis autem vel eum iriure dolor in hendrerit.</p>
    </section>

    <section class="col col-video">
      <h2 class="col-title">Lorem Ipsum Dolor</h2>
      <div class="video-frame">
        <div class="video-still" role="img" aria-label="Video still of a man in a suit signing documents">
          <svg width="44" height="44" viewBox="0 0 44 44" aria-hidden="true">
            <circle cx="22" cy="22" r="21" fill="#f15a3b"/>
            <path d="M17 13 L31 22 L17 31 Z" fill="#ffffff"/>
          </svg>
        </div>
      </div>
    </section>

    <section class="col col-points">
      <h2 class="col-title">Lorem Ipsum Dolor</h2>
      <ul class="points">
        <li><svg width="16" height="13" viewBox="0 0 16 13" aria-hidden="true"><path d="M1.5 7 L6 11 L14.5 1.5" fill="none" stroke="#f15a3b" stroke-width="3"/></svg>Lorem ipsum dolor sit amet, consec.</li>
        <li><svg width="16" height="13" viewBox="0 0 16 13" aria-hidden="true"><path d="M1.5 7 L6 11 L14.5 1.5" fill="none" stroke="#f15a3b" stroke-width="3"/></svg>sed diam nonummy nibh euismod.</li>
        <li><svg width="16" height="13" viewBox="0 0 16 13" aria-hidden="true"><path d="M1.5 7 L6 11 L14.5 1.5" fill="none" stroke="#f15a3b" stroke-width="3"/></svg>Lorem ipsum dolor sit amet, consec.</li>
        <li><svg width="16" height="13" viewBox="0 0 16 13" aria-hidden="true"><path d="M1.5 7 L6 11 L14.5 1.5" fill="none" stroke="#f15a3b" stroke-width="3"/></svg>sed diam nonummy nibh euismod.</li>
        <li><svg width="16" height="13" viewBox="0 0 16 13" aria-hidden="true"><path d="M1.5 7 L6 11 L14.5 1.5" fill="none" stroke="#f15a3b" stroke-width="3"/></svg>Lorem ipsum dolor sit amet, consec.</li>
        <li><svg width="16" height="13" viewBox="0 0 16 13" aria-hidden="true"><path d="M1.5 7 L6 11 L14.5 1.5" fill="none" stroke="#f15a3b" stroke-width="3"/></svg>sed diam nonummy nibh euismod.</li>
      </ul>
    </section>
  </main>

  <footer class="site-footer">
    <div class="copyright">Copyright 2016 Local Election. All rights reserved.</div>
    <a class="donate" href="#">Donate Now</a>
  </footer>
</body>
</html>
```